Working Capital graphics

Our business advisory firm requires 9 images to be re-created and improved in the branding of our business.

The 9 images have been uploaded below and the colours and branding of the business can be found at the website www.tallowmereadvisory.com.au

```html
<!DOCTYPE html>
<html lang="en">
<head>
<meta charset="utf-8">
<title>Payables Drivers</title>
<link href="https://fonts.googleapis.com/css2?family=Montserrat:wght@500;600;700&display=swap" rel="stylesheet">
<style>
  :root {
    --navy-deep: #1b2850;
    --navy-title: #1a2a50;
    --driver-blue: #233f8a;
    --accent-orange: #f7931e;
    --connector-grey: #9a9a9a;
    --white: #ffffff;
  }
  html, body {
    margin: 0;
    padding: 0;
    width: 1200px;
    height: 580px;
    overflow: hidden;
    background: var(--white);
  }
  .driver-chart {
    display: block;
    width: 1200px;
    height: 580px;
    font-family: "Montserrat", sans-serif;
  }
  .chart-title {
    fill: var(--navy-title);
    font-size: 31px;
    font-weight: 700;
    letter-spacing: 1.5px;
  }
  .hub-ring { fill: var(--white); stroke: var(--navy-deep); stroke-width: 1.5; }
  .hub-core { fill: var(--navy-deep); }
  .hub-label {
    fill: var(--white);
    font-size: 13px;
    font-weight: 600;
    letter-spacing: 0.5px;
  }
  .connector {
    fill: none;
    stroke: var(--connector-grey);
    stroke-width: 1.5;
  }
  .connector-label {
    fill: var(--connector-grey);
    font-size: 23px;
    font-weight: 600;
    letter-spacing: 1px;
  }
  .driver-card { fill: var(--driver-blue); }
  .driver-badge-ring { fill: var(--white); stroke: var(--navy-deep); stroke-width: 1.5; }
  .driver-badge { fill: var(--accent-orange); }
  .driver-number {
    fill: var(--white);
    font-size: 25px;
    font-weight: 600;
  }
  .driver-label {
    fill: var(--white);
    font-size: 17px;
    font-weight: 500;
    letter-spacing: 0.6px;
  }
</style>
</head>
<body>
<svg class="driver-chart" viewBox="0 0 1200 580" xmlns="http://www.w3.org/2000/svg" role="img" aria-label="Payables drivers diagram">
  <text class="chart-title" x="601" y="96" text-anchor="middle">PAYABLES</text>

  <g class="hub">
    <circle class="hub-ring" cx="601" cy="194" r="79"/>
    <circle class="hub-core" cx="601" cy="194" r="66"/>
    <text class="hub-label" x="601" y="191" text-anchor="middle">PAYABLES</text>
    <text class="hub-label" x="601" y="206" text-anchor="middle">DRIVERS</text>
  </g>

  <g class="connectors">
    <line class="connector" x1="601" y1="273" x2="601" y2="284"/>
    <text class="connector-label" x="601" y="305" text-anchor="middle">DRIVERS</text>
    <path class="connector" d="M170,370 V326 Q170,313 183,313 H1020 Q1033,313 1033,326 V370"/>
    <line class="connector" x1="386" y1="313" x2="386" y2="370"/>
    <line class="connector" x1="601" y1="313" x2="601" y2="370"/>
    <line class="connector" x1="817" y1="313" x2="817" y2="370"/>
  </g>

  <g class="driver">
    <rect class="driver-card" x="70" y="400" width="200" height="112" rx="17"/>
    <circle class="driver-badge-ring" cx="170" cy="389" r="33"/>
    <circle class="driver-badge" cx="170" cy="389" r="26"/>
    <text class="driver-number" x="170" y="398" text-anchor="middle">14</text>
    <text class="driver-label" x="170" y="442" text-anchor="middle">REDUCE</text>
    <text class="driver-label" x="170" y="460" text-anchor="middle">EARLY</text>
    <text class="driver-label" x="170" y="478" text-anchor="middle">PAYMENTS</text>
  </g>

  <g class="driver">
    <rect class="driver-card" x="286" y="400" width="200" height="112" rx="17"/>
    <circle class="driver-badge-ring" cx="386" cy="389" r="33"/>
    <circle class="driver-badge" cx="386" cy="389" r="26"/>
    <text class="driver-number" x="386" y="398" text-anchor="middle">15</text>
    <text class="driver-label" x="386" y="451" text-anchor="middle">REDUCE</text>
    <text class="driver-label" x="386" y="469" text-anchor="middle">OVER-RIDES</text>
  </g>

  <g class="driver">
    <rect class="driver-card" x="501" y="400" width="200" height="112" rx="17"/>
    <circle class="driver-badge-ring" cx="601" cy="389" r="33"/>
    <circle class="driver-badge" cx="601" cy="389" r="26"/>
    <text class="driver-number" x="601" y="398" text-anchor="middle">16</text>
    <text class="driver-label" x="601" y="442" text-anchor="middle">REDUCE</text>
    <text class="driver-label" x="601" y="460" text-anchor="middle">VENDOR</text>
    <text class="driver-label" x="601" y="478" text-anchor="middle">CREDITS</text>
  </g>

  <g class="driver">
    <rect class="driver-card" x="717" y="400" width="200" height="112" rx="17"/>
    <circle class="driver-badge-ring" cx="817" cy="389" r="33"/>
    <circle class="driver-badge" cx="817" cy="389" r="26"/>
    <text class="driver-number" x="817" y="398" text-anchor="middle">17</text>
    <text class="driver-label" x="817" y="442" text-anchor="middle">INCREASE</text>
    <text class="driver-label" x="817" y="460" text-anchor="middle">PO VENDOR</text>
    <text class="driver-label" x="817" y="478" text-anchor="middle">TERMS</text>
  </g>

  <g class="driver">
    <rect class="driver-card" x="933" y="400" width="200" height="112" rx="17"/>
    <circle class="driver-badge-ring" cx="1033" cy="389" r="33"/>
    <circle class="driver-badge" cx="1033" cy="389" r="26"/>
    <text class="driver-number" x="1033" y="398" text-anchor="middle">18</text>
    <text class="driver-label" x="1033" y="442" text-anchor="middle">INCREASE</text>
    <text class="driver-label" x="1033" y="460" text-anchor="middle">INVOICE ONLY</text>
    <text class="driver-label" x="1033" y="478" text-anchor="middle">TERMS</text>
  </g>
</svg>
</body>
</html>
```